Personal Injury Lawyer Billboard

I would like a design created featuring the image of the lawyer centered in the middle of the design.
To the left of the lawyer's image it should read "INJURED?"
To the right of the lawyer's image, it should read "CALL DEAN!"
Under Call Dean, include the phone number 318-555-0187.
At the bottom of the design include the lawyers information "Dean Marlowe Accident & Injury Lawyers"
PLEASE REMOVED THE BACKGROUND IMAGERY OF THE PHOTO SUBMITTED. Also, the colors for this design should match the colors shown in the logo (navy, white and relective soft gold). Please use those color combinations in ways that best stand out.

```html
<!DOCTYPE html>
<html lang="en">
<head>
<meta charset="utf-8">
<title>Dean Marlowe Billboard Concepts</title>
<link rel="stylesheet" href="https://fonts.googleapis.com/css2?family=Libre+Baskerville:wght@700&family=Lato:wght@400;700&display=swap">
<style>
  :root {
    --navy: #0d1a3d;
    --gold: #b8962e;
    --gold-light: #e9cf7a;
    --white: #ffffff;
    --page: #ffffff;
  }
  html, body {
    margin: 0;
    padding: 0;
    width: 1200px;
    height: 238px;
    overflow: hidden;
    background: var(--page);
  }
  .board-row { position: relative; width: 1200px; height: 238px; }
  .billboard {
    position: absolute;
    top: 29.8px;
    width: 356.6px;
    height: 178px;
    box-shadow: 0 0 3px rgba(0,0,0,0.18);
  }
  .billboard--classic { left: 30.7px; }
  .billboard--spotlight { left: 421.6px; }
  .billboard--wave { left: 812.5px; }
  .headline { font-family: "Libre Baskerville", Georgia, serif; font-weight: 700; font-size: 31px; }
  .phone { font-family: "Lato", Arial, sans-serif; font-weight: 400; font-size: 27px; letter-spacing: 0.5px; }
  .firm-mark { font-family: "Libre Baskerville", Georgia, serif; font-weight: 700; font-size: 21px; fill: var(--white); }
  .firm-line { font-family: "Libre Baskerville", Georgia, serif; font-weight: 700; font-size: 22px; fill: var(--white); }
  .firm-line--small { font-size: 16px; }
  .ink-navy { fill: var(--navy); }
  .ink-white { fill: var(--white); }
  .ink-gold { fill: var(--gold); }
</style>
</head>
<body>
<div class="board-row">

  <!-- Concept 1: classic -->
  <svg class="billboard billboard--classic" viewBox="0 0 765 382" xmlns="http://www.w3.org/2000/svg">
    <defs>
      <linearGradient id="portraitTone1" x1="0" y1="0" x2="0" y2="1">
        <stop offset="0" stop-color="#8a6a55"/>
        <stop offset="0.35" stop-color="#2a3466"/>
        <stop offset="1" stop-color="#1a2450"/>
      </linearGradient>
    </defs>
    <rect width="765" height="382" fill="var(--white)"/>
    <rect class="portrait" x="272" y="5" width="226" height="260" fill="url(#portraitTone1)" role="img" aria-label="Portrait of the lawyer in a navy suit, raising a fist"/>
    <rect y="264" width="765" height="12" class="ink-gold"/>
    <rect y="276" width="765" height="106" class="ink-navy"/>
    <text class="headline ink-navy" x="128" y="141" text-anchor="middle">INJURED?</text>
    <rect x="52" y="150" width="150" height="3" class="ink-gold"/>
    <text class="headline ink-navy" x="722" y="112" text-anchor="end">CALL DEAN!</text>
    <rect x="532" y="124" width="190" height="3" class="ink-gold"/>
    <text class="phone ink-navy" x="722" y="162" text-anchor="end">318-555-0187</text>
    <rect x="285" y="237" width="195" height="69" fill="var(--navy)" stroke="var(--gold)" stroke-width="2.5" rx="2"/>
    <text class="firm-mark" x="383" y="279" text-anchor="middle">DEAN MARLOWE</text>
    <text class="firm-line" x="383" y="354" text-anchor="middle">DEAN MARLOWE ACCIDENT &amp; INJURY LAWYERS</text>
  </svg>

  <!-- Concept 2: spotlight -->
  <svg class="billboard billboard--spotlight" viewBox="0 0 765 382" xmlns="http://www.w3.org/2000/svg">
    <defs>
      <linearGradient id="goldSheen" x1="0" y1="0" x2="1" y2="1">
        <stop offset="0" stop-color="#a8812a"/>
        <stop offset="0.45" stop-color="var(--gold-light)"/>
        <stop offset="1" stop-color="#a8812a"/>
      </linearGradient>
      <linearGradient id="portraitTone2" x1="0" y1="0" x2="0" y2="1">
        <stop offset="0" stop-color="#8a6a55"/>
        <stop offset="0.35" stop-color="#2a3466"/>
        <stop offset="1" stop-color="#1a2450"/>
      </linearGradient>
    </defs>
    <rect width="765" height="382" fill="var(--navy)"/>
    <path d="M280,0 L486,0 L486,110 C486,205 600,245 765,290 L765,382 L647,382 L520,264 L247,264 L120,382 L0,382 L0,268 C160,228 280,205 280,110 Z" fill="url(#goldSheen)"/>
    <rect class="portrait" x="277" y="5" width="210" height="260" fill="url(#portraitTone2)" role="img" aria-label="Portrait of the lawyer in a navy suit, raising a fist"/>
    <text class="headline ink-white" x="128" y="118" text-anchor="middle">INJURED?</text>
    <rect x="52" y="129" width="150" height="3" class="ink-gold"/>
    <text class="headline ink-white" x="722" y="108" text-anchor="end">CALL DEAN!</text>
    <rect x="532" y="120" width="190" height="3" class="ink-gold"/>
    <text class="phone ink-gold" x="722" y="156" text-anchor="end">318-555-0187</text>
    <text class="firm-mark" x="385" y="300" text-anchor="middle">DEAN MARLOWE</text>
    <text class="firm-line firm-line--small" x="385" y="351" text-anchor="middle">DEAN MARLOWE ACCIDENT</text>
    <text class="firm-line firm-line--small" x="385" y="372" text-anchor="middle">&amp; INJURY LAWYERS</text>
  </svg>

  <!-- Concept 3: wave -->
  <svg class="billboard billboard--wave" viewBox="0 0 765 382" xmlns="http://www.w3.org/2000/svg">
    <defs>
      <linearGradient id="portraitTone3" x1="0" y1="0" x2="0" y2="1">
        <stop offset="0" stop-color="#8a6a55"/>
        <stop offset="0.35" stop-color="#2a3466"/>
        <stop offset="1" stop-color="#1a2450"/>
      </linearGradient>
    </defs>
    <rect width="765" height="382" fill="var(--white)"/>
    <rect class="portrait" x="272" y="5" width="226" height="260" fill="url(#portraitTone3)" role="img" aria-label="Portrait of the lawyer in a navy suit, raising a fist"/>
    <path d="M0,170 Q383,333 765,172 L765,382 L0,382 Z" class="ink-gold"/>
    <path d="M0,198 Q383,320 765,195 L765,382 L0,382 Z" class="ink-navy"/>
    <text class="headline ink-navy" x="127" y="73" text-anchor="middle">INJURED?</text>
    <rect x="52" y="85" width="150" height="3" class="ink-gold"/>
    <text class="headline ink-navy" x="722" y="74" text-anchor="end">CALL DEAN!</text>
    <rect x="532" y="85" width="190" height="3" class="ink-gold"/>
    <text class="phone ink-navy" x="722" y="122" text-anchor="end">318-555-0187</text>
    <text class="firm-mark" x="384" y="299" text-anchor="middle">DEAN MARLOWE</text>
    <text class="firm-line" x="384" y="364" text-anchor="middle">DEAN MARLOWE ACCIDENT &amp; INJURY LAWYERS</text>
  </svg>

</div>
</body>
</html>
```